High value cover design for an A4 ideation pad.

The product is NOT A BOOK.

It's an A4 ideation pad for professionals, designers and creators who handwrite their ideas. Visualise creators like Milo Varnet, Owen Plaskit and Gregor Lunwick in your mind's eye.

I'm looking for a cover design for the ideation pad. Both front and back.

It should look, feel and convey the following.

--> A handcrafted product experience

--> High value & Elegance

--> Inspiration

Mandatory --> See Uploaded Files --> Files 1, 5 & 6

Target Market(s)

- Designers

-Creative Professionals

- Entrepreneurs

who handwrite their ideas. Visualise creators like Milo Varnet, Owen Plaskit and Gregor Lunwick in your mind's eye.

Industry/Entity Type

Stationary

Font styles to use
Script
Other font styles liked:
• Calligraphy

Colors
fbed22

Requirements
Must have
• Title text - Quiet Kettle Notes

-Text in gold on brown leather background to convey high value for the front cover.

--> High value & Elegance

--> Inspiration

--> Should compel the customers to pick up and own the idea pad
Nice to have
• That's my take but other ideas are welcome
Should not have
• Must not convey

- low value

```html
<!DOCTYPE html>
<html lang="en">
<head>
<meta charset="utf-8">
<title>Quiet Kettle Notes – Ideation Pad Covers</title>
<link rel="stylesheet" href="https://fonts.googleapis.com/css2?family=Cinzel:wght@400;700&family=Pinyon+Script&display=swap">
<style>
  :root {
    --paper: #f2f1ef;
    --leather: #2a1d15;
    --leather-light: #3d2b1f;
    --leather-dark: #1c130d;
    --gold: #d4ae48;
    --gold-light: #f3db7c;
    --gold-deep: #a87a1e;
  }
  * { margin: 0; padding: 0; box-sizing: border-box; }
  html, body { width: 1200px; height: 742px; overflow: hidden; }
  body {
    position: relative;
    background: var(--paper);
    font-family: "Cinzel", serif;
    color: var(--gold);
  }
  .cover {
    position: absolute;
    top: 88px;
    width: 396px;
    height: 537px;
    background:
      repeating-radial-gradient(circle at 30% 40%, rgba(255,255,255,0.018) 0 1px, transparent 1px 4px),
      repeating-radial-gradient(circle at 70% 65%, rgba(0,0,0,0.08) 0 1px, transparent 1px 5px),
      radial-gradient(ellipse at 50% 35%, var(--leather-light), var(--leather) 60%, var(--leather-dark) 100%);
    box-shadow: 0 10px 18px rgba(0,0,0,0.18);
  }
  .cover--front { left: 86px; }
  .cover--back { left: 685px; }

  .frame-line { position: absolute; background: linear-gradient(90deg, var(--gold-deep), var(--gold-light), var(--gold-deep)); }
  .frame-line--top { left: 19px; right: 19px; top: 20px; height: 2px; }
  .frame-line--left, .frame-line--right {
    top: 20px; bottom: 35px; width: 2px;
    background: linear-gradient(180deg, var(--gold-deep), var(--gold-light) 50%, var(--gold-deep));
  }
  .frame-line--left { left: 19px; }
  .frame-line--right { right: 19px; }
  .frame-line--bottom-left { left: 19px; width: 120px; bottom: 35px; height: 2px; }
  .frame-line--bottom-right { right: 19px; width: 120px; bottom: 35px; height: 2px; }

  .ornament {
    position: absolute;
    left: 50%;
    transform: translateX(-50%);
    background: radial-gradient(ellipse at center, rgba(243,219,124,0.75), rgba(168,122,30,0.45) 60%, transparent 100%);
  }
  .ornament--base { bottom: 34px; width: 100px; height: 24px; }
  .ornament--divider { top: 318px; width: 70px; height: 22px; }

  .title { position: absolute; left: 0; right: 0; text-align: center; color: var(--gold); font-weight: 400; }
  .title__upper { top: 200px; font-size: 21px; letter-spacing: 11px; padding-left: 11px; }
  .title__lower {
    top: 214px; font-family: "Pinyon Script", cursive; font-size: 86px; line-height: 1.1;
    color: var(--gold-light);
  }

  .divider {
    position: absolute; top: 310px; left: 84px; width: 228px; height: 2px;
    background: linear-gradient(90deg, transparent, var(--gold) 8%, var(--gold) 92%, transparent);
  }

  .back-name {
    position: absolute; top: 369px; left: 0; right: 0; text-align: center;
    font-weight: 700; font-size: 21px; letter-spacing: 3px; color: var(--gold);
  }
  .contact-row {
    position: absolute; top: 404px; left: 0; right: 0;
    display: flex; justify-content: center; gap: 18px;
    font-size: 12px; letter-spacing: 1.5px; color: var(--gold);
  }
  .contact-item { display: flex; align-items: center; gap: 5px; }
  .contact-icon { width: 15px; height: 15px; display: block; }
  .web-address {
    position: absolute; top: 444px; left: 0; right: 0; text-align: center;
    font-size: 11px; letter-spacing: 4.5px; color: var(--gold);
  }
</style>
</head>
<body>
  <section class="cover cover--front" aria-label="Front cover">
    <div class="frame-line frame-line--top"></div>
    <div class="frame-line frame-line--left"></div>
    <div class="frame-line frame-line--right"></div>
    <div class="frame-line frame-line--bottom-left"></div>
    <div class="frame-line frame-line--bottom-right"></div>

    <h1 class="title title__upper">QUIET KETTLE</h1>
    <p class="title title__lower">Notes</p>

    <div class="divider"></div>
    <div class="ornament ornament--divider" role="img" aria-label="Gold filigree flourish below the divider"></div>
    <div class="ornament ornament--base" role="img" aria-label="Gold filigree flourish set into the bottom frame"></div>
  </section>

  <section class="cover cover--back" aria-label="Back cover">
    <div class="frame-line frame-line--top"></div>
    <div class="frame-line frame-line--left"></div>
    <div class="frame-line frame-line--right"></div>
    <div class="frame-line frame-line--bottom-left"></div>
    <div class="frame-line frame-line--bottom-right"></div>

    <h2 class="back-name">QUIET KETTLE NOTES</h2>
    <div class="contact-row">
      <span class="contact-item">
        <svg class="contact-icon" viewBox="0 0 16 16" aria-hidden="true">
          <rect width="16" height="16" rx="3" fill="#d4ae48"/>
          <path d="M4.5 3.5l2 .2.8 2.3-1.2 1a6 6 0 0 0 2.9 2.9l1-1.2 2.3.8.2 2a1 1 0 0 1-1 1A8.5 8.5 0 0 1 3.5 4.5a1 1 0 0 1 1-1z" fill="#2a1d15"/>
        </svg>
        55501 20483
      </span>
      <span class="contact-item">
        <svg class="contact-icon" viewBox="0 0 16 16" aria-hidden="true">
          <rect width="16" height="16" rx="3" fill="#d4ae48"/>
          <rect x="3" y="4.5" width="10" height="7" rx="1" fill="none" stroke="#2a1d15" stroke-width="1.5"/>
          <path d="M3.5 5l4.5 3.5L12.5 5" fill="none" stroke="#2a1d15" stroke-width="1.5"/>
        </svg>
        QUIETKETTLE@MAIL
      </span>
    </div>
    <p class="web-address">WWW.QUIETKETTLENOTES.COM</p>

    <div class="ornament ornament--base" role="img" aria-label="Gold filigree flourish set into the bottom frame"></div>
  </section>
</body>
</html>
```